8x8 Social Media Ad - Brant Summit Expo

Attention Real Estate Agents
Please join us for our
Quarterly Real Estate Training Expo
The 2nd Saturday of February, May, August and November
Our Next Training Expo is _________________________________
From 9 am to 1 pm
at
Halvorne Suites Millbrook Court
4817 Copper Willow Lane, Dunmere, MD 20588
Scheduled Speakers
9:00 am - Marcus Pellington - Orientation
9:30 am - Derrin Oakfield - Multiple Income Streams / Crest Program
10:00 am - Talia Brennick - Marketing though Social Media
10:45 am - Rex Dunmore - Generating Business through Ru-Plaza
11:30 am - Kemi Adeyoro - Real Estate Investing
12:15 pm - Gregor Tamsey - (Main Speaker) Training Topic TBA
For more information call Marcus Pellington at (240) 555-0183 or email mpellington@brantsummithomes.example

```html
<!DOCTYPE html>
<html lang="en">
<head>
<meta charset="utf-8">
<title>Brant Summit Expo – Quarterly Real Estate Training Expo</title>
<link rel="stylesheet" href="https://fonts.googleapis.com/css2?family=Archivo:wght@400;700;800&family=Exo+2:wght@800;900&family=Allura&display=swap">
<style>
  :root {
    --teal-deep: #0b5f68;
    --teal: #118d9a;
    --teal-mid: #2aa3ae;
    --teal-light: #5fcfdb;
    --teal-soft: #8fd3da;
    --card: rgba(205, 236, 240, 0.72);
    --ink: #0a0a0a;
    --white: #ffffff;
    --warning: #ffcc00;
    --black: #000000;
  }
  * { box-sizing: border-box; margin: 0; padding: 0; }
  html, body { width: 1200px; height: 1200px; overflow: hidden; background: var(--white); }
  .ad {
    position: relative; width: 1200px; height: 1200px; overflow: hidden;
    background: linear-gradient(180deg, var(--teal) 0%, #1a9aa6 35%, #3fb1bb 55%, var(--teal-mid) 100%);
    font-family: "Archivo", Arial, sans-serif; color: var(--ink);
  }
  .city-backdrop {
    position: absolute; left: 0; top: 480px; width: 1200px; height: 598px;
    background: linear-gradient(180deg, rgba(60,170,180,0) 0%, rgba(40,150,160,0.55) 45%, rgba(10,100,110,0.85) 100%);
  }
  .title-band {
    position: absolute; left: 0; top: 59px; width: 1200px; height: 80px;
    background: var(--teal-deep);
    border-top: 3px solid var(--teal-mid); border-bottom: 3px solid var(--teal-mid);
  }
  .warning-icon { position: absolute; left: 67px; top: 24px; width: 160px; height: 143px; }
  .attention {
    position: absolute; left: 246px; top: 70px; width: 880px;
    font-family: "Exo 2", sans-serif; font-weight: 800; font-size: 55px; line-height: 60px;
    color: var(--teal-light); letter-spacing: 1px; white-space: nowrap;
  }
  .headline {
    position: absolute; left: 244px; top: 158px;
    font-family: "Exo 2", sans-serif; font-weight: 900; font-size: 86px; line-height: 88px;
    color: var(--white); text-shadow: 3px 4px 6px rgba(0,40,45,0.55); white-space: nowrap;
  }
  .invite {
    position: absolute; left: 58px; top: 196px; width: 260px;
    font-family: "Allura", cursive; font-size: 56px; line-height: 52px;
    color: rgba(225,245,248,0.8); transform: rotate(-9deg); transform-origin: left top;
  }
  .invite span { display: block; padding-left: 26px; }
  .info-icon { position: absolute; left: 72px; }
  .info { position: absolute; left: 144px; white-space: nowrap; line-height: 1; }
  .info.big { font-weight: 800; font-size: 34px; }
  .info.small { font-weight: 400; font-size: 25px; }
  .info.venue { font-weight: 800; font-size: 27px; }
  .info sup { font-size: 18px; vertical-align: 14px; }
  .blank { display: inline-block; width: 425px; border-bottom: 1.5px solid var(--ink); height: 20px; vertical-align: -2px; }
  .speakers-label {
    position: absolute; left: 46px; top: 945px; width: 320px;
    font-family: "Allura", cursive; font-size: 58px; line-height: 60px; color: var(--white);
    transform: rotate(-90deg); transform-origin: left top; white-space: nowrap;
  }
  .speaker { position: absolute; top: 600px; width: 146px; text-align: center; }
  .speaker .portrait {
    position: relative; z-index: 2; width: 118px; height: 118px; margin: 0 auto;
    border-radius: 50%; border: 3px solid var(--teal-mid);
    background: radial-gradient(circle at 50% 40%, #6a5a52 0%, #3b2f2b 55%, #21aab6 56%, #1c9aa5 100%);
  }
  .speaker .card {
    position: relative; z-index: 1; margin-top: -34px; height: 301px;
    border-radius: 73px; background: var(--card); padding: 52px 8px 0;
  }
  .speaker .time { font-weight: 800; font-size: 25px; line-height: 30px; }
  .speaker .name { font-weight: 800; font-size: 25px; line-height: 28px; padding-top: 4px; }
  .speaker .role { font-weight: 400; font-size: 20px; line-height: 23px; }
  .speaker hr { border: 0; border-top: 2px solid rgba(255,255,255,0.9); margin: 4px 6px 4px; }
  .speaker .topic { font-weight: 800; font-size: 20px; line-height: 24.5px; padding-top: 2px; }
  .footer {
    position: absolute; left: 0; top: 1076px; width: 1200px; height: 124px;
    background: var(--black); border-top: 3px solid var(--teal-mid);
  }
  .contact-icon {
    position: absolute; top: 1027px; width: 57px; height: 57px; border-radius: 50%;
    background: var(--teal-light); display: flex; align-items: center; justify-content: center;
  }
  .contact {
    position: absolute; left: 76px; top: 1098px; font-size: 27px; line-height: 33px;
    color: var(--teal-light); white-space: nowrap;
  }
  .contact b { color: var(--white); font-weight: 700; }
  .brand {
    position: absolute; left: 890px; top: 1098px; display: flex; align-items: center; gap: 10px;
  }
  .brand .mark { width: 26px; height: 26px; background: var(--teal-light); }
  .brand .name { font-weight: 800; font-size: 24px; line-height: 28px; color: var(--white); white-space: nowrap; }
</style>
</head>
<body>
<main class="ad">
  <div class="city-backdrop" role="img" aria-label="Aerial photo of a dense city skyline with hills, tinted teal"></div>

  <div class="title-band"></div>
  <svg class="warning-icon" viewBox="0 0 160 143" aria-hidden="true">
    <path d="M80 8 Q88 4 94 12 L154 120 Q160 136 142 138 L18 138 Q0 136 6 120 L66 12 Q72 4 80 8 Z" fill="var(--warning)"/>
    <rect x="70" y="34" width="20" height="64" rx="3" fill="var(--teal-deep)"/>
    <rect x="70" y="106" width="20" height="18" rx="2" fill="var(--teal-deep)"/>
  </svg>
  <h2 class="attention">Attention Real Estate Agents</h2>

  <p class="invite">Please join<span>us for our</span></p>
  <h1 class="headline">Quarterly Real Estate<br>Training Expo</h1>

  <svg class="info-icon" style="top:361px" width="50" height="50" viewBox="0 0 50 50" aria-hidden="true">
    <rect x="4" y="8" width="42" height="38" rx="4" fill="none" stroke="var(--teal-soft)" stroke-width="3"/>
    <rect x="4" y="8" width="42" height="9" fill="var(--teal-soft)"/>
    <rect x="12" y="2" width="4" height="10" fill="var(--teal-soft)"/><rect x="34" y="2" width="4" height="10" fill="var(--teal-soft)"/>
    <g fill="var(--teal-soft)"><rect x="10" y="22" width="6" height="5"/><rect x="19" y="22" width="6" height="5"/><rect x="28" y="22" width="6" height="5"/><rect x="37" y="22" width="5" height="5"/><rect x="10" y="31" width="6" height="5"/><rect x="19" y="31" width="6" height="5"/><rect x="28" y="31" width="6" height="5"/></g>
  </svg>
  <p class="info big" style="top:359px">The 2<sup>nd</sup> Saturday of February, May, August and November</p>
  <p class="info small" style="top:403px">Our Next Training Expo is <span class="blank"></span></p>

  <svg class="info-icon" style="top:424px" width="50" height="50" viewBox="0 0 50 50" aria-hidden="true">
    <circle cx="25" cy="25" r="22" fill="none" stroke="var(--teal-soft)" stroke-width="3"/>
    <circle cx="25" cy="25" r="16" fill="none" stroke="var(--teal-soft)" stroke-width="2"/>
    <path d="M25 14 V25 L32 31" fill="none" stroke="var(--teal-soft)" stroke-width="3" stroke-linecap="round"/>
  </svg>
  <p class="info big" style="top:436px">From 9 am to 1 pm</p>
  <p class="info small" style="top:475px">at</p>

  <svg class="info-icon" style="top:502px" width="54" height="54" viewBox="0 0 54 54" aria-hidden="true">
    <path d="M4 50 L12 30 L22 33 L32 30 L42 33 L50 50 Z" fill="var(--teal-soft)"/>
    <path d="M27 4 C19 4 15 10 15 15 C15 23 27 34 27 34 C27 34 39 23 39 15 C39 10 35 4 27 4 Z" fill="var(--teal-soft)"/>
    <circle cx="27" cy="15" r="4.5" fill="var(--teal)"/>
  </svg>
  <p class="info venue" style="top:504px">Halvorne Suites Millbrook Court</p>
  <p class="info venue" style="top:535px">4817 Copper Willow Lane, Dunmere, MD 20588</p>

  <p class="speakers-label">Scheduled Speakers</p>

  <section class="speaker" style="left:145px">
    <div class="portrait" role="img" aria-label="Portrait photo of Marcus Pellington"></div>
    <div class="card"><p class="time">9:00 am</p><hr><p class="name">Marcus Pellington</p><hr><p class="topic">Orientation</p></div>
  </section>
  <section class="speaker" style="left:312px">
    <div class="portrait" role="img" aria-label="Portrait photo of Derrin Oakfield"></div>
    <div class="card"><p class="time">9:30 am</p><hr><p class="name">Derrin Oakfield</p><hr><p class="topic">Multiple Income Streams/ Crest Program</p></div>
  </section>
  <section class="speaker" style="left:479px">
    <div class="portrait" role="img" aria-label="Portrait photo of Talia Brennick"></div>
    <div class="card"><p class="time">10:00 am</p><hr><p class="name">Talia Brennick</p><hr><p class="topic">Marketing through Social Media</p></div>
  </section>
  <section class="speaker" style="left:646px">
    <div class="portrait" role="img" aria-label="Portrait photo of Rex Dunmore"></div>
    <div class="card"><p class="time">10:45 am</p><hr><p class="name">Rex Dunmore</p><hr><p class="topic">Generating Business through Ru-Plaza</p></div>
  </section>
  <section class="speaker" style="left:813px">
    <div class="portrait" role="img" aria-label="Portrait photo of Kemi Adeyoro"></div>
    <div class="card"><p class="time">11:30 am</p><hr><p class="name">Kemi Adeyoro</p><hr><p class="topic">Real Estate Investing</p></div>
  </section>
  <section class="speaker" style="left:980px">
    <div class="portrait" role="img" aria-label="Portrait photo of Gregor Tamsey"></div>
    <div class="card"><p class="time">12:15 pm</p><hr><p class="name">Gregor Tamsey</p><p class="role">(Main Speaker)</p><hr><p class="topic">Training Topic TBA</p></div>
  </section>

  <footer class="footer"></footer>
  <div class="contact-icon" style="left:80px">
    <svg width="30" height="30" viewBox="0 0 24 24" aria-hidden="true"><path d="M6.6 10.8c1.4 2.8 3.8 5.1 6.6 6.6l2.2-2.2c.3-.3.7-.4 1-.2 1.1.4 2.3.6 3.6.6.6 0 1 .4 1 1V20c0 .6-.4 1-1 1C10.6 21 3 13.4 3 4c0-.6.4-1 1-1h3.5c.6 0 1 .4 1 1 0 1.3.2 2.5.6 3.6.1.3 0 .7-.2 1l-2.3 2.2z" fill="var(--black)"/></svg>
  </div>
  <div class="contact-icon" style="left:146px">
    <svg width="32" height="24" viewBox="0 0 32 24" aria-hidden="true"><rect x="1.5" y="1.5" width="29" height="21" fill="none" stroke="var(--black)" stroke-width="2.5"/><path d="M2 2 L16 14 L30 2 M2 22 L12 11 M30 22 L20 11" fill="none" stroke="var(--black)" stroke-width="2.5"/></svg>
  </div>
  <p class="contact">For more information call <b>Marcus Pellington</b> at <b>(240) 555-0183</b><br>or email <b>mpellington@brantsummithomes.example</b></p>
  <div class="brand"><span class="mark"></span><span class="name">Brant Summit<br>Expo</span></div>
</main>
</body>
</html>
```